Business Card Design for Varomir Facility Services

We are looking for a Business Card Design for the Company "Varomir Facility Services."
Front side:
- Company Logo (small)
- Company Name, address, pohone, website and personal data.
- white background, for text e.g. company colors (blue or green like in the logo)
Please use following data:
Company data:
Varomir Facility Services Kostelac
Birkenhaldweg 14
6342 Lindmatt
www.varomir-fs.ch
Person data:
Tarik Kostelac
Geschäftsführer
+41 76 519 47 83
info@varomir-fs.ch
Back side:
could be colored in blue or green
please use a big logo sing and some smaller icons to say what is all beeing offered in facility services, like cleaning, maintenance cleaning
industrial cleaning, caretaking, gardening, disposal. There is no need for everyone of the icons if there are similar or an icon is standing for more of them.
colors to use:
blue: HEX 246BB0
green: HEX 52B33E

```html
<!DOCTYPE html>
<html lang="de">
<head>
<meta charset="utf-8">
<title>Varomir Facility Services – Visitenkarte</title>
<link rel="stylesheet" href="https://fonts.googleapis.com/css2?family=Lato:wght@400;700;900&display=swap">
<style>
  :root {
    --blue: #246BB0;
    --green: #52B33E;
    --green-deep: #1faa4a;
    --ink: #555a60;
    --white: #ffffff;
    --stage: #3a3c40;
  }
  * { box-sizing: border-box; margin: 0; padding: 0; }
  html, body { width: 1200px; height: 900px; overflow: hidden; }
  body {
    background: var(--stage);
    font-family: "Lato", Arial, sans-serif;
    position: relative;
  }
  .card {
    position: absolute;
    width: 620px;
    height: 380px;
    border-radius: 34px;
    overflow: hidden;
  }
  /* Back side */
  .card-back {
    left: 70px; top: 50px;
    background: var(--green);
    color: var(--white);
  }
  .back-brand {
    position: absolute;
    top: 92px; left: 0; right: 0;
    display: flex; align-items: center; justify-content: center; gap: 16px;
  }
  .brand-dot {
    width: 34px; height: 34px; border-radius: 50%;
    flex: none;
  }
  .card-back .brand-dot { background: var(--white); }
  .back-brand .brand-name {
    font-weight: 700; font-size: 34px; letter-spacing: 1px;
    color: var(--white);
  }
  .services {
    position: absolute;
    left: 30px; right: 30px; bottom: 70px;
    display: flex; justify-content: space-between;
    list-style: none;
  }
  .service {
    width: 104px;
    display: flex; flex-direction: column; align-items: center; gap: 12px;
    font-size: 14px; text-align: center; line-height: 1.2;
  }
  .service-icon {
    width: 46px; height: 46px; border-radius: 50%;
    background: radial-gradient(circle at 40% 35%, #3d86cc, var(--blue));
    box-shadow: 0 2px 3px rgba(0,0,0,.25);
  }
  /* Front side */
  .card-front {
    left: 510px; top: 470px;
    background: var(--white);
    color: var(--ink);
  }
  .front-brand {
    position: absolute; top: 44px; right: 40px;
    display: flex; align-items: center; gap: 12px;
  }
  .card-front .brand-dot { background: var(--blue); width: 30px; height: 30px; }
  .front-brand .brand-name {
    font-weight: 700; font-size: 26px; color: var(--blue); letter-spacing: .5px;
  }
  .divider {
    position: absolute; left: 40px; right: 40px; top: 112px;
    height: 2px; background: var(--green);
  }
  .person { position: absolute; left: 40px; top: 140px; }
  .person-name {
    font-weight: 900; font-size: 24px; color: var(--green); letter-spacing: .5px;
    text-transform: uppercase;
  }
  .person-role { font-size: 17px; color: var(--blue); margin-top: 4px; }
  .person-rule { width: 190px; height: 2px; background: var(--green); margin: 10px 0 12px; }
  .contact { list-style: none; font-size: 16px; line-height: 26px; }
  .contact li { display: flex; align-items: center; gap: 10px; }
  .contact svg { width: 14px; height: 14px; flex: none; fill: var(--blue); }
  .web-domain { color: var(--green); }
  .company {
    position: absolute; right: 40px; top: 244px;
    text-align: right; font-size: 16px; line-height: 22px; font-style: normal;
  }
  .company-name { color: var(--blue); }
  .footer-band {
    position: absolute; left: 0; right: 0; bottom: 0; height: 42px;
    display: flex;
  }
  .band-green { flex: 1; background: linear-gradient(90deg, var(--green-deep), var(--green)); }
  .band-street {
    width: 230px; background: var(--blue); color: var(--white);
    font-size: 16px; display: flex; align-items: center; justify-content: center;
    border-left: 4px solid var(--white);
  }
  .band-end { width: 36px; background: var(--green); border-left: 4px solid var(--white); }
</style>
</head>
<body>

<section class="card card-back" aria-label="Rückseite">
  <div class="back-brand">
    <span class="brand-dot"></span>
    <span class="brand-name">Varomir Facility Services</span>
  </div>
  <ul class="services">
    <li class="service"><span class="service-icon" role="img" aria-label="Icon Unterhaltsreinigung"></span>Maintenance cleaning</li>
    <li class="service"><span class="service-icon" role="img" aria-label="Icon Industriereinigung"></span>Industrial cleaning</li>
    <li class="service"><span class="service-icon" role="img" aria-label="Icon Hauswartung"></span>Caretaking</li>
    <li class="service"><span class="service-icon" role="img" aria-label="Icon Gartenpflege"></span>Gardening</li>
    <li class="service"><span class="service-icon" role="img" aria-label="Icon Entsorgung"></span>Disposal</li>
  </ul>
</section>

<section class="card card-front" aria-label="Vorderseite">
  <div class="front-brand">
    <span class="brand-dot"></span>
    <span class="brand-name">Varomir Facility Services</span>
  </div>
  <div class="divider"></div>

  <div class="person">
    <p class="person-name">Tarik Kostelac</p>
    <p class="person-role">Geschäftsführer</p>
    <div class="person-rule"></div>
    <ul class="contact">
      <li>
        <svg viewBox="0 0 24 24" aria-hidden="true"><path d="M6.6 10.8a15.1 15.1 0 0 0 6.6 6.6l2.2-2.2a1 1 0 0 1 1-.25 11.4 11.4 0 0 0 3.6.57 1 1 0 0 1 1 1V20a1 1 0 0 1-1 1A17 17 0 0 1 3 4a1 1 0 0 1 1-1h3.5a1 1 0 0 1 1 1c0 1.25.2 2.45.57 3.57a1 1 0 0 1-.25 1z"/></svg>
        +41 76 519 47 83
      </li>
      <li>
        <svg viewBox="0 0 24 24" aria-hidden="true"><path d="M2 5h20v14H2zm2 2v.5l8 5 8-5V7l-8 5z"/></svg>
        info@varomir-fs.ch
      </li>
      <li>
        <svg viewBox="0 0 24 24" aria-hidden="true"><path d="M12 2a10 10 0 1 0 0 20 10 10 0 0 0 0-20zm6.9 6h-3a15 15 0 0 0-1.3-3.9A8 8 0 0 1 18.9 8zM12 4c.8 1.2 1.5 2.5 1.9 4h-3.8c.4-1.5 1.1-2.8 1.900-4zM4.3 14a8 8 0 0 1 0-4h3.4a16 16 0 0 0 0 4zm.8 2h3a15 15 0 0 0 1.3 3.9A8 8 0 0 1 5.1 16zm3-8h-3a8 8 0 0 1 4.3-3.9A15 15 0 0 0 8.1 8zM12 20c-.8-1.2-1.5-2.5-1.9-4h3.8c-.4 1.5-1.1 2.8-1.9 4zm2.3-6H9.7a14 14 0 0 1 0-4h4.6a14 14 0 0 1 0 4zm.3 5.9a15 15 0 0 0 1.3-3.9h3a8 8 0 0 1-4.3 3.9zM16.3 14a16 16 0 0 0 0-4h3.4a8 8 0 0 1 0 4z"/></svg>
        <span>www.<span class="web-domain">varomir-fs.ch</span></span>
      </li>
    </ul>
  </div>

  <address class="company">
    6342 Lindmatt<br>
    <span class="company-name">Varomir Facility</span><br>
    Services Kostelac
  </address>

  <div class="footer-band">
    <div class="band-green"></div>
    <div class="band-street">Birkenhaldweg 14</div>
    <div class="band-end"></div>
  </div>
</section>

</body>
</html>
```